Health Care Company with Logo Needs Business Cards designed

We are a luxury behavioral health company looking for business cards design we already have a logo and are looking for someone to design a sophisticated luxurious looking business card. Please note that Card design should be captivating just like the logo and also encompass the logo color

Industry/Entity Type

Healthcare

Contact Information for Business Card

Logo,company name, tagline, my name and title, contact details, and physical address

```html
<!DOCTYPE html>
<html lang="en">
<head>
<meta charset="utf-8">
<title>Corvin Behavioral Health – Business Cards</title>
<link rel="stylesheet" href="https://fonts.googleapis.com/css2?family=Roboto+Condensed:wght@500;700&family=Roboto:wght@500&family=Open+Sans:wght@400&display=swap">
<style>
  :root {
    --backdrop: #353535;
    --card: #262626;
    --card-back: #252525;
    --emboss: #111111;
    --mark-dark: #1b1b1b;
    --white: #e9e9e9;
    --muted: #cfcfcf;
    --purple: #7b3d8f;
    --blue: #1e8fcf;
    --orange: #e08a1e;
    --green: #7fae2e;
  }
  * { margin: 0; padding: 0; box-sizing: border-box; }
  html, body { width: 1200px; height: 1138px; overflow: hidden; }
  body { background: var(--backdrop); position: relative; font-family: "Open Sans", sans-serif; }

  .card {
    position: absolute;
    border-radius: 16px;
    overflow: hidden;
  }
  .card--front { left: 274px; top: 186px; width: 624px; height: 376px; background: var(--card); }
  .card--back  { left: 276px; top: 608px; width: 618px; height: 374px; background: var(--card-back); }

  /* front */
  .front__square {
    position: absolute; left: 252px; top: 62px; width: 120px; height: 120px;
    background: var(--mark-dark);
  }
  .front__name {
    position: absolute; left: 0; right: 0; top: 248px; text-align: center;
    font-family: "Roboto Condensed", sans-serif; font-weight: 700; font-size: 36px;
    color: var(--emboss); letter-spacing: 0.5px;
  }
  .front__tagline {
    position: absolute; left: 0; right: 0; top: 340px; text-align: center;
    font-family: "Roboto Condensed", sans-serif; font-weight: 700; font-size: 12px;
    letter-spacing: 3.2px; color: var(--white);
  }

  /* back */
  .brand { position: absolute; left: 37px; top: 53px; display: flex; align-items: flex-start; }
  .brand__square { width: 74px; height: 74px; background: var(--orange); margin-right: 19px; }
  .brand__name {
    font-family: "Roboto Condensed", sans-serif; font-weight: 700; font-size: 38px;
    line-height: 1; color: var(--purple); margin-top: 4px;
  }
  .brand__tagline {
    font-family: "Roboto Condensed", sans-serif; font-weight: 700; font-size: 12px;
    letter-spacing: 3.1px; color: var(--blue); margin-top: 8px;
  }
  .holder {
    position: absolute; left: 37px; top: 252px;
    font-family: "Roboto", sans-serif; font-weight: 500; font-size: 22px; color: var(--purple);
  }
  .contact {
    position: absolute; left: 37px; top: 296px;
    font-size: 14px; line-height: 22px; color: var(--muted);
  }
  .stripe { position: absolute; left: 0; right: 0; bottom: 0; height: 7px; display: flex; }
  .stripe span { flex: 1; }
  .stripe .orange { background: var(--orange); }
  .stripe .blue { background: var(--blue); }
  .stripe .green { background: var(--green); }
  .stripe .purple { background: var(--purple); }
</style>
</head>
<body>
  <section class="card card--front">
    <div class="front__square"></div>
    <div class="front__name">Corvin Behavioral Health</div>
    <div class="front__tagline">DEDICATED TO HOPE, HEALING AND RECOVERY</div>
  </section>

  <section class="card card--back">
    <div class="brand">
      <div class="brand__square"></div>
      <div>
        <div class="brand__name">Corvin Behavioral Health</div>
        <div class="brand__tagline">DEDICATED TO HOPE, HEALING AND RECOVERY</div>
      </div>
    </div>
    <div class="holder">DANIEL REYES</div>
    <div class="contact">
      <p>P: 000-111-0000 &nbsp;| &nbsp;E: hello@corvinbehavioral.com &nbsp;| &nbsp;W: www.corvinbehavioral.com</p>
      <p>A: 123, Anywhere ST, Any City, Any Town, US 123456</p>
    </div>
    <div class="stripe">
      <span class="orange"></span><span class="blue"></span><span class="green"></span><span class="purple"></span>
    </div>
  </section>
</body>
</html>
```